New Business Card Design for Manufacturing

We are an engineering/manufacturing company that offers Advanced machining/assembly/engineering services, as well as innovative products for the heavy duty engine cooling markets.

We are looking to get a new business card designed that is clean and modern looking, but still fits the wide range of technical/skilled work we do.

- We hope to use this design as the base for other design work in new Presentations, web, and print work.

Industry/Entity Type

Engineering

Contact Information for Business Card

Our preferred color of blue is (RGB) 22/71/159 but can vary slightly from that color. Our content will be our Logo and full company name (Vantrell Forge Works, Inc.), company address, name, job title, phone number with extension, cell number, fax number, website, and email address on the cards.
We'd like the full company name next to the logo, but we are open to other interpretations of that layout.
Preferably, we would like the back side to be clean with just our logo, and the front to contain all of the contact information.

Colors
2f74b4
0355a3
85abd2

Requirements
Must have
• - Logo, company name, needed content - We are open to interpretation beyond that.
• - Standard size business card.
• - Horizontal orientation.
• - Enough space for lengthy names / job titles (for example, a job title could read "Directory of Human Resources" or "V.P. of Governmental Affairs"). We need this to look clean, whether the title be short (CEO) or long (as described above).

```html
<!DOCTYPE html>
<html lang="en">
<head>
<meta charset="utf-8">
<title>Vantrell Forge Works – Business Card</title>
<link rel="stylesheet" href="https://fonts.googleapis.com/css2?family=Roboto:wght@400;700&family=Roboto+Condensed:wght@500&display=swap">
<style>
  :root {
    --backdrop: #e8e5e1;
    --card-white: #fbfbfb;
    --card-grey: #7b8187;
    --brand-blue: #1450a3;
    --text-grey: #555a5f;
    --tagline-grey: #8a8e93;
    --white: #ffffff;
  }
  html, body {
    margin: 0;
    width: 1200px;
    height: 960px;
    overflow: hidden;
    background: var(--backdrop);
    font-family: "Roboto", Arial, sans-serif;
  }
  .canvas { position: relative; width: 1200px; height: 960px; }
  .card {
    position: absolute;
    width: 600px;
    height: 342px;
    border-radius: 22px;
    overflow: hidden;
    box-shadow: 0 3px 6px rgba(0,0,0,0.25);
  }
  .card-front { left: 302px; top: 129px; background: var(--card-white); }
  .card-back { left: 299px; top: 488px; background: var(--card-grey); }

  .front-brand { position: absolute; left: 53px; top: 48px; }
  .brand-name {
    margin: 0;
    font-weight: 700;
    font-size: 38px;
    line-height: 34px;
    letter-spacing: 0.5px;
    color: var(--brand-blue);
    text-transform: uppercase;
  }
  .tagline {
    margin: 8px 0 0;
    font-weight: 700;
    font-size: 14px;
    color: var(--tagline-grey);
    text-transform: uppercase;
  }

  .address {
    position: absolute; left: 53px; top: 177px;
    margin: 0; font-style: normal;
    font-size: 14.5px; line-height: 18px; color: var(--text-grey);
  }
  .contact-list {
    position: absolute; left: 53px; top: 222px;
    margin: 0; padding: 0; list-style: none;
    font-size: 14.5px; line-height: 19.3px; color: var(--text-grey);
  }
  .contact-list li { display: flex; align-items: center; }
  .contact-list svg { width: 13px; height: 13px; margin-right: 7px; fill: var(--brand-blue); }

  .name-band { position: absolute; left: 338px; top: 204px; width: 262px; height: 69px; }
  .name-band svg { position: absolute; inset: 0; }
  .name-band .person {
    position: absolute; right: 34px; top: 9px; text-align: right; color: var(--white);
  }
  .person-name {
    margin: 0; font-family: "Roboto Condensed", Arial, sans-serif;
    font-weight: 500; font-size: 25px; line-height: 28px;
  }
  .person-title { margin: 2px 0 0; font-size: 14px; }

  .back-lockup {
    position: absolute; left: 106px; top: 130px;
    display: flex; align-items: flex-start; gap: 18px; color: var(--white);
  }
  .back-lockup .brand-name { color: var(--white); font-size: 50px; line-height: 56px; }
  .back-lockup .tagline { color: var(--white); margin-top: 4px; }
  .company-full {
    margin: 2px 0 0; font-weight: 700; font-size: 18px; line-height: 20px;
    text-transform: uppercase;
  }
</style>
</head>
<body>
<main class="canvas">
  <section class="card card-front" aria-label="Card front">
    <div class="front-brand">
      <p class="brand-name">Vantrell<br>Forge</p>
      <p class="tagline">Built for What's Next</p>
    </div>

    <address class="address">4120 Ridgeway Court<br>Fairbanks, Alaska 99701</address>

    <ul class="contact-list">
      <li><svg viewBox="0 0 16 16" aria-hidden="true"><path d="M3.6 1l2.6 2.9-1.5 2a9 9 0 0 0 5.4 5.4l2-1.5L15 12.4l-1.7 2.3C7 14.6 1.4 9 1.3 2.7z"/></svg>555 214 7730</li>
      <li><svg viewBox="0 0 16 16" aria-hidden="true"><path d="M4 0h8a1 1 0 0 1 1 1v14a1 1 0 0 1-1 1H4a1 1 0 0 1-1-1V1a1 1 0 0 1 1-1zm1 2v10h6V2zm3 11a1 1 0 1 0 0 2 1 1 0 0 0 0-2z"/></svg>555 380 6142</li>
      <li><svg viewBox="0 0 16 16" aria-hidden="true"><path d="M1 4h14v9H1zm1 1l6 4 6-4z" fill-rule="evenodd"/></svg>dorian@vantrellforge.com</li>
      <li><svg viewBox="0 0 16 16" aria-hidden="true"><circle cx="8" cy="8" r="7"/></svg>www.vantrellforge.com</li>
    </ul>

    <div class="name-band">
      <svg viewBox="0 0 262 69" width="262" height="69" aria-hidden="true">
        <polygon points="14,0 262,0 262,69 0,69" fill="var(--brand-blue)"/>
      </svg>
      <div class="person">
        <p class="person-name">DORIAN KELLER</p>
        <p class="person-title">V.P. of Governmental Affairs</p>
      </div>
    </div>
  </section>

  <section class="card card-back" aria-label="Card back">
    <div class="back-lockup">
      <div>
        <p class="brand-name">Vantrell</p>
        <p class="tagline">Built for What's Next</p>
      </div>
      <p class="company-full">Vantrell<br>Forge Works<br>Inc.</p>
    </div>
  </section>
</main>
</body>
</html>
```